Business Card for Coastal Tundrabridge Advisory

We need a business card for Coastal Tundrabridge Advisory. The company website address is provided below. The company logo is attached. We provide specialized permafrost services to the mining, transportation, and oil & gas industries. The card should be prepared for:
Matthias Korhonen, PhD.
Coastal Tundrabridge Advisory
PO Box 418259
Quillwater, Alaska 99642
Direct: +1-907-555-0143
Email: mkorhonen@tundrabridgeadvisory.example
Website: www.coastaltundrabridgeadvisory.example

```html
<!DOCTYPE html>
<html lang="en">
<head>
<meta charset="utf-8">
<title>Coastal Tundrabridge Advisory — Business Card</title>
<link rel="stylesheet" href="https://fonts.googleapis.com/css2?family=Roboto:wght@300;400;500;700&display=swap">
<style>
  :root {
    --backdrop: #262626;
    --card: #111722;
    --card-edge: #0c1119;
    --ink: #f2f4f7;
    --ink-soft: #c9ced6;
    --rule: #6f7682;
    --pattern-blue: #2f7fb3;
    --pattern-deep: #1a2433;
  }
  * { box-sizing: border-box; margin: 0; padding: 0; }
  html, body {
    width: 1200px; height: 780px; overflow: hidden;
    background: var(--backdrop);
    font-family: "Roboto", Arial, sans-serif;
    color: var(--ink);
  }
  .sheet {
    width: 1200px; height: 780px;
    display: flex; align-items: center; justify-content: center; gap: 40px;
  }
  .card {
    position: relative;
    width: 560px; height: 320px;
    background: var(--card);
    box-shadow: 0 18px 40px rgba(0,0,0,.55);
    overflow: hidden;
  }

  /* Front */
  .brand {
    position: absolute; left: 36px; top: 0; bottom: 0; width: 190px;
    display: flex; align-items: center;
  }
  .brand-name {
    font-weight: 500; font-size: 22px; line-height: 1.2;
    letter-spacing: .04em; text-transform: uppercase; color: var(--ink);
  }
  .divider {
    position: absolute; left: 248px; top: 58px; width: 1px; height: 150px;
    background: var(--rule);
  }
  .person { position: absolute; left: 276px; top: 56px; right: 20px; }
  .person-name { font-size: 26px; line-height: 1.1; white-space: nowrap; }
  .person-name .given { font-weight: 700; }
  .person-name .family { font-weight: 300; }
  .person-title { font-weight: 700; font-size: 15px; margin-top: 2px; }
  .contacts { list-style: none; margin-top: 16px; }
  .contacts li {
    display: flex; align-items: center; gap: 8px;
    font-size: 10.5px; font-weight: 400; color: var(--ink-soft);
    line-height: 20px; white-space: nowrap;
  }
  .contacts svg { width: 11px; height: 11px; flex: none; }
  .address {
    position: absolute; left: 276px; bottom: 34px;
    font-size: 12px; font-weight: 400; color: var(--ink-soft);
  }

  /* Back */
  .pattern-field {
    position: absolute; inset: 0;
    background:
      radial-gradient(ellipse at 35% 30%, rgba(47,127,179,.55), transparent 55%),
      linear-gradient(160deg, var(--pattern-deep) 0%, var(--card) 70%);
  }
  .back-brand {
    position: absolute; right: 28px; top: 38px; width: 170px;
    font-weight: 500; font-size: 13px; line-height: 1.2;
    letter-spacing: .04em; text-transform: uppercase; text-align: right;
    color: var(--ink);
  }
  .services { position: absolute; left: 0; right: 0; bottom: 30px; text-align: center; }
  .services-title { font-weight: 700; font-size: 13px; letter-spacing: .02em; }
  .services-text { font-weight: 400; font-size: 12px; margin-top: 6px; color: var(--ink); }
</style>
</head>
<body>
<main class="sheet">
  <section class="card card-front" aria-label="Card front">
    <div class="brand"><p class="brand-name">Coastal Tundrabridge Advisory</p></div>
    <div class="divider"></div>
    <div class="person">
      <h1 class="person-name"><span class="given">Matthias</span> <span class="family">Korhonen</span></h1>
      <p class="person-title">PhD</p>
      <ul class="contacts">
        <li>
          <svg viewBox="0 0 24 24" fill="var(--ink)"><path d="M6.6 10.8a15 15 0 0 0 6.6 6.6l2.2-2.2a1 1 0 0 1 1-.25 11.4 11.4 0 0 0 3.6.57 1 1 0 0 1 1 1V20a1 1 0 0 1-1 1A17 17 0 0 1 3 4a1 1 0 0 1 1-1h3.5a1 1 0 0 1 1 1c0 1.25.2 2.45.57 3.57a1 1 0 0 1-.25 1z"/></svg>
          +1-907-555-0143
        </li>
        <li>
          <svg viewBox="0 0 24 24" fill="none" stroke="var(--ink)" stroke-width="2"><rect x="3" y="5" width="18" height="14" rx="1"/><path d="M3 6l9 7 9-7"/></svg>
          mkorhonen@tundrabridgeadvisory.example
        </li>
        <li>
          <svg viewBox="0 0 24 24" fill="none" stroke="var(--ink)" stroke-width="2"><circle cx="12" cy="12" r="9"/><path d="M3 12h18M12 3a14 14 0 0 1 0 18M12 3a14 14 0 0 0 0 18"/></svg>
          www.coastaltundrabridgeadvisory.example
        </li>
      </ul>
    </div>
    <p class="address">PO Box 418259 Quillwater, Alaska 99642</p>
  </section>

  <section class="card card-back" aria-label="Card back">
    <div class="pattern-field" role="img" aria-label="Repeating company name pattern in blue and dark navy tones"></div>
    <p class="back-brand">Coastal Tundrabridge Advisory</p>
    <div class="services">
      <h2 class="services-title">OUR SERVICES</h2>
      <p class="services-text">We provide specialized permafrost services to the mining, transportation, and oil &amp; gas industries</p>
    </div>
  </section>
</main>
</body>
</html>
```